A clean crisp business card for a Landscape Construction company. Designed to be easy to read contact/ info and also be appealing/interesting, unlike a traditional business card.

Industry/Entity Type

Landscape Construction

Contact Information for Business Card

Company name : Brambleford Landscape Construction, phone number: (877) 62Vista, website:Bramblefordyards.example, Email, sales@bramblefordyards.example

Requirements
Nice to have
• Luxurious finishes/ details…. Icons or emblems next to contact info
Should not have
• Clipart or general pictures

```html
<!DOCTYPE html>
<html lang="en">
<head>
<meta charset="utf-8">
<title>Brambleford Landscape Construction – Business Card</title>
<link rel="stylesheet" href="https://fonts.googleapis.com/css2?family=Cinzel:wght@600&family=Roboto:wght@400;500;700&display=swap">
<style>
  :root {
    --stage: #1c1c1d;
    --card: #232324;
    --card-back: #1e1e1f;
    --blue: #1577cf;
    --green: #9fd028;
    --white: #f4f4f4;
    --muted: #9a9a9a;
    --emboss: #3a3a3c;
    --divider: #5a5a5c;
  }
  * { margin: 0; padding: 0; box-sizing: border-box; }
  html, body {
    width: 1200px; height: 874px; overflow: hidden;
    background: var(--stage);
  }
  .canvas {
    position: relative; width: 1200px; height: 874px;
    display: flex; flex-direction: column; align-items: center;
    justify-content: center; gap: 48px;
  }
  .card {
    position: relative; width: 620px; height: 354px;
    border-radius: 22px; overflow: hidden;
    box-shadow: 0 18px 40px rgba(0,0,0,.55);
  }
  /* Back side */
  .card-back {
    background: var(--card-back);
    display: flex; align-items: center; justify-content: center; gap: 18px;
  }
  .back-mark {
    width: 46px; height: 46px; border-radius: 50%;
    background: var(--emboss);
  }
  .back-name {
    font-family: "Cinzel", serif; font-weight: 600;
    font-size: 30px; letter-spacing: 2px; color: var(--emboss);
  }
  /* Front side */
  .card-front { background: var(--card); }
  .front-body {
    position: absolute; left: 0; top: 0; width: 100%; height: 230px;
    display: flex; align-items: center; justify-content: center;
  }
  .brand {
    width: 230px; display: flex; align-items: center; gap: 10px;
    padding-right: 22px;
  }
  .brand-dot {
    flex: none; width: 14px; height: 14px; border-radius: 50%;
    background: var(--blue);
  }
  .brand-name {
    font-family: "Cinzel", serif; font-weight: 600;
    font-size: 17px; line-height: 1.25; color: var(--blue);
  }
  .divider {
    width: 1px; height: 96px; background: var(--divider);
  }
  .contact { padding-left: 24px; width: 300px; }
  .person {
    font-family: "Cinzel", serif; font-weight: 600; font-size: 22px;
    letter-spacing: 1px;
  }
  .person-first { color: var(--blue); }
  .person-last { color: var(--green); }
  .role {
    font-family: "Roboto", sans-serif; font-weight: 700;
    font-size: 14px; color: var(--white); margin-bottom: 10px;
  }
  .contact-line {
    font-family: "Roboto", sans-serif; font-weight: 400;
    font-size: 13px; color: var(--white); line-height: 1.45;
  }
  .wave { position: absolute; left: 0; bottom: 0; width: 620px; height: 140px; }
  .website {
    position: absolute; right: 48px; bottom: 22px;
    font-family: "Roboto", sans-serif; font-weight: 500;
    font-size: 15px; color: var(--white);
  }
</style>
</head>
<body>
<main class="canvas">
  <section class="card card-back" aria-label="Card back">
    <span class="back-mark"></span>
    <span class="back-name">Brambleford</span>
  </section>

  <section class="card card-front" aria-label="Card front">
    <div class="front-body">
      <div class="brand">
        <span class="brand-dot"></span>
        <span class="brand-name">Brambleford Landscape Construction</span>
      </div>
      <div class="divider"></div>
      <div class="contact">
        <div class="person"><span class="person-first">Daniel</span> <span class="person-last">Hartwell</span></div>
        <div class="role">President</div>
        <div class="contact-line">(877) 62Vista</div>
        <div class="contact-line">sales@bramblefordyards.example</div>
      </div>
    </div>

    <svg class="wave" viewBox="0 0 620 140" preserveAspectRatio="none" aria-hidden="true">
      <path d="M0 10 C 120 70, 260 78, 400 76 C 500 75, 570 90, 620 130 L620 140 L0 140 Z" fill="var(--blue)"/>
      <path d="M0 4 C 120 62, 260 70, 400 68 C 500 67, 570 82, 620 122" fill="none" stroke="var(--green)" stroke-width="6"/>
    </svg>
    <div class="website">Bramblefordyards.example</div>
  </section>
</main>
</body>
</html>
```